Flyer Design for Private Car Service

Flyer should cater to Business Travelers and Executives who travel Business Class or First Class.
Flyer should include images attached.
Flyer should include the below text
Dallas to Austin
Quorvan Ride
• Travel Dallas to Austin in a new 2025 Norvak Tressel for $499 one-way
• Trip includes a Uniformed Chauffeur who has a Commercial Drivers License (CDL)
• You can Schedule Chauffeur Pickup at Your Home in Dallas
• Our Chauffeur will Drop You Off at Your Final Destination in Austin
• You can Schedule Chauffeur Return Pickup in Austin and Return Back to Dallas.
• We offer Faster Times on Door-to-Door Travel than Bluequill Airways
• We offer Comparable Prices on Door-to-Door Travel Times than Bluequill Airways
• All of our trips are insured with $500k of commercial auto insurance
• Our Passengers can Talk on Cell Phone & Conduct Kavlo calls Throughout Travel
• Our Passengers have Maximum Privacy, Comfort and First-Class Amenities.
• Our Passengers Avoid Marrow Pike Airfield and QHN Airport hassles & delays
• Member Tellbrook Chamber of Commerce, Pindle Chamber of Commerce.
• Book your trip today at www.quorvanride.example
Target Market(s)
Business Travelers
Look and feel

```html
<!DOCTYPE html>
<html lang="en">
<head>
<meta charset="utf-8">
<title>Dallas to Austin – Quorvan Ride</title>
<link rel="stylesheet" href="https://fonts.googleapis.com/css2?family=Cinzel:wght@400;700&family=Fira+Sans:wght@400;500;700&display=swap">
<style>
  :root {
    --red: #e8262b;
    --black: #000000;
    --ink: #1c1c1c;
    --white: #ffffff;
    --rule: #9c3a3a;
  }
  * { margin: 0; padding: 0; box-sizing: border-box; }
  html, body { width: 927px; height: 1200px; overflow: hidden; background: var(--white); }
  .flyer { position: relative; width: 927px; height: 1200px; overflow: hidden; background: var(--white); font-family: "Fira Sans", Arial, sans-serif; color: var(--ink); }
  .hero { position: absolute; left: 0; top: 0; width: 927px; height: 510px; }
  .brand { position: absolute; top: 82px; left: 0; width: 927px; text-align: center; font-family: "Cinzel", serif; font-weight: 400; font-size: 32px; letter-spacing: 1px; color: var(--white); }
  .title { position: absolute; top: 536px; left: 0; width: 927px; text-align: center; font-family: "Cinzel", serif; font-weight: 700; font-size: 68px; line-height: 1; color: var(--black); }
  .subtitle-row { position: absolute; top: 612px; left: 48px; width: 831px; display: flex; align-items: center; gap: 12px; }
  .subtitle-row .rule { flex: 1; height: 2px; background: linear-gradient(90deg, transparent, var(--rule)); }
  .subtitle-row .rule.right { background: linear-gradient(90deg, var(--rule), transparent); }
  .subtitle { font-family: "Cinzel", serif; font-weight: 700; font-size: 34px; line-height: 1; color: var(--black); }
  .features { position: absolute; top: 666px; list-style: none; width: 400px; }
  .features.left { left: 48px; }
  .features.right { left: 480px; width: 410px; }
  .features li { position: relative; padding-left: 28px; height: 74px; font-size: 17px; line-height: 25px; }
  .features li::before { content: ""; position: absolute; left: 0; top: 10px; width: 14px; height: 14px; border-radius: 50%; background: var(--black); }
  .features.right li::before { background: var(--red); }
  .cta-panel { position: absolute; left: 44px; top: 1039px; width: 838px; height: 200px; background: var(--black); border: 5px solid var(--red); border-radius: 24px; color: var(--white); text-align: center; }
  .cta-panel p { font-weight: 500; font-size: 18.5px; letter-spacing: 0.3px; }
  .cta-panel .note-1 { margin-top: 28px; }
  .cta-panel .note-2 { margin-top: 10px; }
  .book-button { position: absolute; left: 155px; top: 110px; width: 519px; height: 80px; background: var(--red); border-radius: 14px; font-weight: 700; font-size: 21px; padding-top: 9px; }
</style>
</head>
<body>
<main class="flyer">
  <svg class="hero" viewBox="0 0 927 510">
    <defs>
      <linearGradient id="fleetTone" x1="0" y1="0" x2="1" y2="1">
        <stop offset="0" stop-color="#6f6b69"/>
        <stop offset="0.6" stop-color="#4a4746"/>
        <stop offset="1" stop-color="#5a3b3b"/>
      </linearGradient>
      <linearGradient id="greetTone" x1="0" y1="0" x2="1" y2="1">
        <stop offset="0" stop-color="#8a8886"/>
        <stop offset="0.5" stop-color="#3a3838"/>
        <stop offset="1" stop-color="#5c5855"/>
      </linearGradient>
    </defs>
    <path d="M0,0 H927 V310 C790,398 620,444 420,445 L300,445 L0,268 Z" fill="var(--black)"/>
    <path d="M0,0 H927 V215 C810,345 640,410 430,412 L300,412 L0,245 Z" fill="var(--red)"/>
    <path d="M0,0 H925 C880,200 700,392 430,404 L300,404 L0,232 Z" fill="url(#fleetTone)" role="img" aria-label="Photo of uniformed chauffeurs standing beside a fleet of SUVs outside an office building"/>
    <path d="M250,158 C330,150 370,200 420,225 C470,245 490,270 485,320 C482,350 455,355 445,365 L444,412 C420,470 340,502 260,502 C180,502 100,470 78,420 L72,410 L72,360 C40,330 28,300 30,270 C34,215 90,200 140,190 C180,180 205,162 250,158 Z" fill="url(#greetTone)" stroke="var(--red)" stroke-width="9" role="img" aria-label="Photo of a chauffeur helping a business traveler with luggage beside a black SUV"/>
  </svg>

  <div class="brand">Quorvan Ride</div>

  <h1 class="title">Dallas to Austin</h1>
  <div class="subtitle-row">
    <span class="rule"></span>
    <h2 class="subtitle">Quorvan Ride</h2>
    <span class="rule right"></span>
  </div>

  <ul class="features left">
    <li>Travel Dallas to Austin in a new 2025 Norvak Tressel for $499 one-way</li>
    <li>Trip includes a Uniformed Chauffeur who has a Commercial Drivers License (CDL)</li>
    <li>You can Schedule Chauffeur Pickup at Your Home in Dallas</li>
    <li>Our Chauffeur will Drop You Off at Your Final Destination in Austin</li>
    <li>You can Schedule Chauffeur Return Pickup in Austin and Return Back to Dallas.</li>
  </ul>
  <ul class="features right">
    <li>We offer Faster Times on Door-to-Door Travel than Bluequill Airways</li>
    <li>We offer Comparable Prices on Door-to-Door Travel Times than Bluequill Airways</li>
    <li>All of our trips are insured with $500k of commercial auto insurance</li>
    <li>Our Passengers can Talk on Cell Phone &amp; Conduct Kavlo calls Throughout Travel</li>
    <li>Our Passengers have Maximum Privacy, Comfort and First-Class Amenities.</li>
  </ul>

  <section class="cta-panel">
    <p class="note-1">Our Passengers Avoid Marrow Pike Airfield and QHN Airport hassles &amp; delays</p>
    <p class="note-2">Member Tellbrook Chamber of Commerce, Pindle Chamber of Commerce.</p>
    <div class="book-button">Book your trip today at www.quorvanride.example</div>
  </section>
</main>
</body>
</html>
```